Fresh Dwelling Tract Guide needs a new Landing Page

I like to get a landing page or website with 2-3 pages to help target home buyers who are looking to buy homes from builders such as TW Residences, Morvik, P.L. Fennick, etc. The landing page/website to be non-cluttered and be able to explain to home buyers that there are many benefits to include me as their buyer's agent when they buy a brand new home from any builders.
I may want to incorporate a short explanation video (animated) on the landing page and then for the viewer to click on a button that will take them to another page where they can search for new homes from different builders.
Target Market(s)
Home buyers looking to buy brand new home from builders such as TW Residences, Morvik, P.L. Fennick, etc.
Industry/Entity Type
Real Estate
Number of Pages Required
2 page
Font styles to use
Requirements
Must have
- The landing page may have the explanation video at the bottom of the landing page (scrolled down) or there may be a CALL TO ACTION button that takes the viewer to the 2nd page to watch the explanation video. Once they watched the explanation video and are still interested, they can click on another CALL TO ACTION button that will take them to another website that they will be able to search for all the available new homes and register their contact information.
Should not have
- No clutters and no dark colors.

```html
<!DOCTYPE html>
<html lang="en">
<head>
<meta charset="utf-8">
<title>Fresh Dwelling Tract</title>
<link href="https://fonts.googleapis.com/css2?family=Montserrat:wght@400;500;600;700&display=swap" rel="stylesheet">
<style>
  :root {
    --orange: #ff7a12;
    --orange-dark: #f26a00;
    --white: #ffffff;
    --white-soft: rgba(255,255,255,0.9);
    --rule: rgba(255,255,255,0.45);
    --sky: #5f6d79;
    --house: #6e6c64;
    --garden: #5d6650;
    --lawn: #4f6b3e;
    --glow: rgba(230,170,100,0.45);
    --play-core: #4a4a4a;
  }
  * { box-sizing: border-box; margin: 0; padding: 0; }
  html, body { width: 1200px; height: 648px; overflow: hidden; }
  body { font-family: "Montserrat", sans-serif; color: var(--white); background: var(--sky); }

  .hero {
    position: relative;
    width: 1200px;
    height: 648px;
    overflow: hidden;
  }
  .hero-backdrop {
    position: absolute;
    inset: 0;
    background:
      radial-gradient(ellipse 360px 200px at 700px 380px, var(--glow), transparent 70%),
      linear-gradient(180deg, var(--sky) 0%, var(--house) 45%, var(--garden) 75%, var(--lawn) 100%);
  }

  .site-header {
    position: absolute;
    top: 28px; left: 99px; right: 99px;
    display: flex;
    justify-content: space-between;
    align-items: center;
  }
  .brand {
    display: flex;
    align-items: center;
    gap: 9px;
    font-weight: 600;
    font-size: 17px;
    line-height: 1;
    color: var(--white);
  }
  .brand-mark {
    width: 16px; height: 16px;
    border: 2px solid var(--orange);
  }
  .header-contact {
    display: flex;
    align-items: center;
    gap: 20px;
    font-weight: 600;
    font-size: 16px;
    letter-spacing: 1.5px;
    color: var(--white-soft);
  }
  .phone { display: flex; align-items: center; gap: 9px; }
  .menu-toggle { display: flex; flex-direction: column; gap: 3px; }
  .menu-toggle span { width: 20px; height: 3px; border-radius: 2px; background: var(--white-soft); }

  .hero-copy {
    position: absolute;
    left: 93px;
    top: 196px;
  }
  .hero-title {
    font-weight: 600;
    font-size: 68px;
    line-height: 0.9;
    letter-spacing: 0.5px;
  }
  .hero-lead {
    margin-top: 22px;
    margin-left: 6px;
    font-size: 22px;
    line-height: 37px;
    font-weight: 400;
    width: 470px;
  }
  .cta {
    display: inline-block;
    margin-top: 26px;
    margin-left: 6px;
    width: 180px;
    height: 50px;
    line-height: 50px;
    text-align: center;
    border-radius: 25px;
    background: linear-gradient(180deg, var(--orange) 0%, var(--orange-dark) 100%);
    color: var(--white);
    font-weight: 600;
    font-size: 16px;
    letter-spacing: 1px;
    text-decoration: none;
  }

  .video-play {
    position: absolute;
    left: 855px; top: 247px;
    width: 136px; height: 136px;
  }

  .site-footer {
    position: absolute;
    left: 0; right: 0; top: 590px;
    height: 58px;
    border-top: 1px solid var(--rule);
    display: flex;
    justify-content: space-between;
    align-items: center;
    padding: 0 99px 0 102px;
    font-size: 13.5px;
  }
  .legal a { color: var(--white); text-decoration: none; }
  .social { display: flex; gap: 18px; font-weight: 600; font-size: 12px; }
  .social a { color: var(--white); text-decoration: none; }
</style>
</head>
<body>
<main class="hero">
  <div class="hero-backdrop" role="img" aria-label="Photograph of a two-storey brick and siding family home at dusk, with warm lit windows, trees and a landscaped front lawn"></div>

  <header class="site-header">
    <div class="brand"><span class="brand-mark"></span>Fresh Dwelling Tract</div>
    <div class="header-contact">
      <span class="phone">
        <svg width="15" height="15" viewBox="0 0 24 24" aria-hidden="true"><path fill="currentColor" d="M6.6 10.8a15.1 15.1 0 0 0 6.6 6.6l2.2-2.2c.3-.3.7-.4 1-.2 1.1.4 2.3.6 3.6.6.6 0 1 .4 1 1V20c0 .6-.4 1-1 1A17 17 0 0 1 3 4c0-.6.4-1 1-1h3.5c.6 0 1 .4 1 1 0 1.3.2 2.5.6 3.6.1.3 0 .7-.2 1z"/></svg>
        Ph:555-014-2286
      </span>
      <span class="menu-toggle" aria-label="Menu"><span></span><span></span><span></span></span>
    </div>
  </header>

  <section class="hero-copy">
    <h1 class="hero-title">Fresh Dwelling<br>Tract</h1>
    <p class="hero-lead">Lorem ipsum dolor sit ameconctetur adipiscing elit, sed do eiusmo.</p>
    <a class="cta" href="#">GET STARTED</a>
  </section>

  <svg class="video-play" viewBox="0 0 136 136" aria-label="Play video">
    <circle cx="68" cy="68" r="68" fill="rgba(255,255,255,0.3)"/>
    <circle cx="68" cy="68" r="58" fill="rgba(255,255,255,0.4)"/>
    <circle cx="68" cy="68" r="41" fill="#4a4a4a"/>
    <path d="M60 51 L84 68 L60 85 Z" fill="#ffffff"/>
  </svg>

  <footer class="site-footer">
    <p class="legal">© 2018 All Rights are Reserved. <a href="#">Privacy Policy</a> | <a href="#">Terms of Use</a> | <a href="#">Contact</a></p>
    <nav class="social">
      <a href="#">Pebble</a>
      <a href="#">Wren</a>
      <a href="#">Linkwell</a>
      <a href="#">Snapfold</a>
    </nav>
  </footer>
</main>
</body>
</html>
```